Homepage for Travel NFT Marketplace

Hi there!
We are building a Travel Marketplace that incorporates NFTs. We are looking for a full page redesign of the homepage for this marketplace.
You can find the instructions along with all the content here at https://www.sharevault.net/sh/7qw3mzx8kpl2vr4/BBHtxLmQpwZeKnaRsTuVwXyhd?dl=0
We look forward to seeing your submissions!
Industry/Entity Type
Tourism
Number of Pages Required
1 page
Font styles to use
Sans Serif
Colors
0094D4
00A9DD
6FCCEA
C7EBF8
E9F6FB
00AB8E
00BBA5
67D7C9
C6EFE9
E9F9F6
F0912C
F2A743
F7CA91
FBE8D2
FDF5EE
A7469A
B969AE
D3A5CF
EDDBEB
F8F0F9
6B429C
8869AF
B7A5CE
E3DAEB
F3F0F8
Requirements
Must have
- Clean, Modern & Fun!
Should not have
- Messy or Overcrowded

```html
<!DOCTYPE html>
<html lang="en">
<head>
<meta charset="utf-8">
<title>Nomad Ledger — Travel NFT Marketplace</title>
<link rel="stylesheet" href="https://fonts.googleapis.com/css2?family=Fredoka:wght@500;600&family=Nunito+Sans:wght@400;600;700&display=swap">
<style>
:root{
  --blue:#3aaef0;
  --sky:#00A9DD;
  --magenta:#e0119f;
  --plum:#b0409e;
  --violet:#a335e6;
  --purple:#6B429C;
  --pink-nav:#d63ec4;
  --ink:#1e1e28;
  --pale:#eee9fb;
  --white:#ffffff;
}
*{margin:0;padding:0;box-sizing:border-box}
html,body{width:1200px;height:3859px;overflow:hidden;background:var(--white)}
body{position:relative;font-family:"Nunito Sans",sans-serif;color:var(--ink)}
.abs{position:absolute}
.display{font-family:"Fredoka",sans-serif;font-weight:600}

/* header */
.site-header{left:0;top:0;width:1200px;height:72px;background:var(--white)}
.brand{left:141px;top:16px;display:flex;align-items:center;gap:10px;font-family:"Fredoka",sans-serif;font-weight:500;font-size:21px;color:var(--violet)}
.brand-dot{width:34px;height:34px;border-radius:50%;background:var(--violet)}
.main-nav{top:28px;left:0;width:1200px;font-size:13px}
.main-nav a{position:absolute;color:var(--ink);text-decoration:none;white-space:nowrap}
.main-nav a.active{color:var(--pink-nav)}
.nav-mark{left:624px;top:12px;width:12px;height:12px;border-radius:50%;background:var(--pink-nav)}
.header-icon{top:24px;width:28px;height:28px;border-radius:50%;background:#efe4f7}
.header-icon::after{content:"";position:absolute;left:8px;top:8px;width:12px;height:12px;border-radius:50%;background:var(--plum)}

/* hero */
.hero-band{left:0;top:72px;width:1200px;height:441px;background:linear-gradient(100deg,var(--blue) 0%,#8d52d9 42%,var(--magenta) 72%,var(--plum) 100%)}
.hero-title{left:141px;top:200px;width:440px;font-size:35px;line-height:46px;color:var(--white);letter-spacing:.3px}
.welcome-title{left:143px;top:710px;font-size:43px;line-height:49px;color:var(--violet)}
.welcome-sub{left:143px;top:820px;font-size:16px;color:var(--ink)}

/* stats */
.stats-band{left:0;top:1045px;width:1200px;height:302px;background:linear-gradient(100deg,var(--blue) 0%,#9a48d8 45%,var(--magenta) 78%,#c8169e 100%)}
.stat{top:1100px;width:240px;text-align:center;color:var(--white)}
.stat-icon{width:96px;height:96px;margin:0 auto 14px;border-radius:50%;background:radial-gradient(circle at 40% 35%,#ff7be3,#a02ec9 70%);display:flex;align-items:center;justify-content:center}
.stat-value{font-size:26px;line-height:30px}
.stat-label{font-size:13px;margin-top:4px}

/* apart */
.section-title{left:0;width:1200px;text-align:center;font-size:42px;color:var(--violet)}
.name-badge{display:flex;align-items:center;justify-content:center;border-radius:50%;background:var(--white);font-family:"Fredoka",sans-serif;font-weight:500;color:var(--violet);text-align:center}
.step-num{width:26px;height:26px;border-radius:50%;background:linear-gradient(135deg,#7a5cf0,var(--magenta));color:var(--white);font-size:12px;font-weight:700;display:flex;align-items:center;justify-content:center}
.step-title{font-size:16px;font-weight:600;line-height:22px}
.step-text{font-size:13px;line-height:19px;margin-top:8px}
.step.right-align{text-align:right}
.step.right-align .step-num{margin-left:auto}
.step .step-num{margin-bottom:14px}

/* nft grid */
.nft{width:214px;height:210px;clip-path:polygon(16% 0,84% 0,100% 16%,100% 84%,84% 100%,16% 100%,0 84%,0 16%)}
.explore-btn{left:534px;top:3646px;width:132px;height:33px;border-radius:17px;background:linear-gradient(90deg,var(--blue),var(--magenta));color:var(--white);font-size:12px;display:flex;align-items:center;justify-content:center}

/* footer */
.site-footer{left:0;top:3765px;width:1200px;height:48px;background:linear-gradient(90deg,#9d3fe0,#7d4fe8 50%,#5f63f0)}
.copyright{left:142px;top:3781px;font-size:12px;color:var(--white)}
.legal{left:739px;top:3781px;font-size:12px;color:var(--white)}
.social{top:3778px;width:23px;height:23px;border-radius:50%;background:var(--white)}
.footer-badge{left:540px;top:3728px;width:120px;height:120px;font-size:16px;box-shadow:0 0 0 6px #f1e4fb}
</style>
</head>
<body>

<!-- Header -->
<header class="abs site-header">
  <div class="abs brand"><span class="brand-dot"></span>Nomad Ledger</div>
  <span class="abs nav-mark"></span>
  <nav class="abs main-nav">
    <a class="active" style="left:611px">About</a>
    <a style="left:686px">NFT</a>
    <a style="left:746px">Trips</a>
    <a style="left:813px">Auctions</a>
    <a style="left:907px">The Pot</a>
  </nav>
  <span class="abs header-icon" style="left:990px"></span>
  <span class="abs header-icon" style="left:1029px"></span>
</header>

<!-- Hero -->
<section class="abs hero-band"></section>
<h1 class="abs display hero-title">Our Adventures Are Available Exclusively To Those Holding A Certain NFT In Their Wallet</h1>

<svg class="abs" style="left:0;top:0" width="1200" height="1000" viewBox="0 0 1200 1000">
  <defs>
    <clipPath id="hexTall"><polygon points="0,-88 76,-44 76,44 0,88 -76,44 -76,-44"/></clipPath>
    <linearGradient id="g-travelers" x1="0" y1="0" x2="0" y2="1"><stop offset="0" stop-color="#cde9fb"/><stop offset="1" stop-color="#e98aa5"/></linearGradient>
    <linearGradient id="g-explorer" x1="0" y1="0" x2="0" y2="1"><stop offset="0" stop-color="#bfe6fb"/><stop offset="1" stop-color="#d8b87a"/></linearGradient>
    <linearGradient id="g-hiker" x1="0" y1="0" x2="0" y2="1"><stop offset="0" stop-color="#d9f0ee"/><stop offset="1" stop-color="#8f9a6b"/></linearGradient>
    <linearGradient id="g-coast" x1="0" y1="0" x2="0" y2="1"><stop offset="0" stop-color="#3c7f5a"/><stop offset="0.5" stop-color="#3a8cb0"/><stop offset="1" stop-color="#e0c23a"/></linearGradient>
    <linearGradient id="g-friends" x1="0" y1="0" x2="0" y2="1"><stop offset="0" stop-color="#bfe3f6"/><stop offset="1" stop-color="#3aa6d0"/></linearGradient>
    <linearGradient id="g-sunset" x1="0" y1="0" x2="0" y2="1"><stop offset="0" stop-color="#f8dfc4"/><stop offset="1" stop-color="#c9873f"/></linearGradient>
  </defs>
  <g fill="none" stroke="#ffffff" stroke-width="1.6" stroke-dasharray="6 4">
    <path d="M709 270 V410 H848"/>
    <path d="M986 270 V410 H848"/>
    <path d="M848 372 V420"/>
  </g>
  <g fill="none" stroke="#d95bc7" stroke-width="1.6" stroke-dasharray="6 4">
    <path d="M805 560 V637 H746 V860"/>
    <path d="M890 560 V637 H952 V860"/>
    <path d="M848 600 V650"/>
  </g>
  <g transform="translate(709 192)" role="img" aria-label="Illustration of a cartoon family of tourists"><rect x="-80" y="-90" width="160" height="180" fill="url(#g-travelers)" clip-path="url(#hexTall)"/></g>
  <g transform="translate(986 192)" role="img" aria-label="Illustration of a cartoon boy traveller with a camera"><rect x="-80" y="-90" width="160" height="180" fill="url(#g-explorer)" clip-path="url(#hexTall)"/></g>
  <g transform="translate(848 298)" role="img" aria-label="Illustration of a cartoon girl hiker with binoculars"><rect x="-80" y="-90" width="160" height="180" fill="url(#g-hiker)" clip-path="url(#hexTall)"/></g>
  <g transform="translate(848 731)" role="img" aria-label="Photo of a woman in a yellow dress above a tropical bay"><rect x="-80" y="-90" width="160" height="180" fill="url(#g-coast)" clip-path="url(#hexTall)"/></g>
  <g transform="translate(745 889)" role="img" aria-label="Photo of friends cheering on a boat at sea"><rect x="-80" y="-90" width="160" height="180" fill="url(#g-friends)" clip-path="url(#hexTall)"/></g>
  <g transform="translate(952 889)" role="img" aria-label="Photo of a hiker raising his arms at sunset"><rect x="-80" y="-90" width="160" height="180" fill="url(#g-sunset)" clip-path="url(#hexTall)"/></g>
</svg>
<div class="abs name-badge" style="left:768px;top:433px;width:160px;height:160px;font-size:21px;box-shadow:0 6px 18px rgba(120,40,160,.25)">Nomad<br>Ledger</div>

<h2 class="abs display welcome-title">Welcome To<br>Nomad Ledger</h2>
<p class="abs welcome-sub">The World’s First Blockchain Travel Marketplace</p>

<!-- Stats -->
<section class="abs stats-band"></section>
<div class="abs stat" style="left:250px">
  <div class="stat-icon"><svg width="48" height="48" viewBox="0 0 48 48" fill="none" stroke="#fff" stroke-width="2"><circle cx="24" cy="18" r="9"/><path d="M24 13v10M21 15.5h4.5a2 2 0 0 1 0 4H22a2 2 0 0 0 0 4h4.5"/><path d="M6 30l8 10h10M42 30l-8 10H24"/></svg></div>
  <div class="stat-value">$1,120,546</div><div class="stat-label">Donated to Charity</div>
</div>
<div class="abs stat" style="left:480px">
  <div class="stat-icon"><svg width="48" height="48" viewBox="0 0 48 48" fill="none" stroke="#fff" stroke-width="2"><circle cx="24" cy="15" r="9"/><path d="M24 10v10M21 12.5h4.5a2 2 0 0 1 0 4H22a2 2 0 0 0 0 4h4.5"/><circle cx="12" cy="34" r="3"/><circle cx="24" cy="34" r="3"/><circle cx="36" cy="34" r="3"/><path d="M7 44a5 5 0 0 1 10 0M19 44a5 5 0 0 1 10 0M31 44a5 5 0 0 1 10 0"/></svg></div>
  <div class="stat-value">$456,060</div><div class="stat-label">Given in Prizes to our Community</div>
</div>
<div class="abs stat" style="left:709px">
  <div class="stat-icon"><svg width="48" height="48" viewBox="0 0 48 48" fill="none" stroke="#fff" stroke-width="2"><path d="M6 8h36v6H6zM10 14v30M38 14v30"/><path d="M14 22h20v16a4 4 0 0 1-4 4H18a4 4 0 0 1-4-4z"/><path d="M24 26c3 3 3 6 0 9-3-3-3-6 0-9z"/></svg></div>
  <div class="stat-value">$56,060</div><div class="stat-label">In the Adventure Pot</div>
</div>

<!-- What sets us apart -->
<h2 class="abs display section-title" style="top:1460px">What Sets Us Apart?</h2>

<svg class="abs" style="left:0;top:1520px" width="1200" height="1490" viewBox="0 1520 1200 1490">
  <defs>
    <linearGradient id="g-forest" x1="0" y1="0" x2="0" y2="1"><stop offset="0" stop-color="#ffffff" stop-opacity="0"/><stop offset="0.45" stop-color="#e6efe6"/><stop offset="1" stop-color="#e9f3f2"/></linearGradient>
    <linearGradient id="g-soft" x1="0" y1="0" x2="1" y2="0"><stop offset="0" stop-color="#f3ecfd"/><stop offset="1" stop-color="#e7f0fd"/></linearGradient>
    <linearGradient id="g-road" x1="0" y1="0" x2="0" y2="1"><stop offset="0" stop-color="#f6e6e9"/><stop offset="0.5" stop-color="#eed3d8"/><stop offset="1" stop-color="#f3e2e5"/></linearGradient>
  </defs>
  <circle cx="1091" cy="1580" r="41" fill="url(#g-soft)"/>
  <rect x="1022" y="1645" width="240" height="62" rx="31" fill="url(#g-soft)"/>
  <rect x="1080" y="1700" width="180" height="115" rx="40" fill="url(#g-soft)"/>
  <rect x="-60" y="2057" width="300" height="58" rx="29" fill="url(#g-soft)"/>
  <rect x="-60" y="2110" width="238" height="118" rx="40" fill="url(#g-soft)"/>
  <circle cx="108" cy="2290" r="41" fill="url(#g-soft)"/>
  <circle cx="881" cy="2425" r="35" fill="url(#g-soft)"/>
  <rect x="1040" y="2337" width="220" height="60" rx="30" fill="url(#g-soft)"/>
  <rect x="1004" y="2395" width="260" height="140" rx="40" fill="url(#g-soft)"/>
  <rect x="0" y="2550" width="1200" height="445" fill="url(#g-forest)" role="img" aria-label="Faded illustration of a pine forest and a river"/>
  <rect x="365" y="1665" width="400" height="1180" rx="24" fill="url(#g-road)" role="img" aria-label="Illustration of a winding red road passing six travel scenes: travellers, a booking screen, a guide with a crowd, a painted camper van, a pool party and a gold coin"/>
</svg>
<div class="abs name-badge" style="left:530px;top:1528px;width:140px;height:140px;font-size:19px;box-shadow:0 4px 14px rgba(120,40,160,.2)">Nomad<br>Ledger</div>

<div class="abs step right-align" style="left:179px;top:1694px;width:290px">
  <div class="step-num">1</div><div class="step-title">The Adventures!</div>
  <p class="step-text">We dig deep in our research &amp; work with local guides to create unique experiences not found anywhere else.</p>
</div>
<div class="abs step" style="left:733px;top:1922px;width:285px">
  <div class="step-num">2</div><div class="step-title">Intentional Travel</div>
  <p class="step-text">We give you the ability to have a meaningful impact on local communities and offset the emissions from your travels.</p>
</div>
<div class="abs step right-align" style="left:177px;top:2094px;width:236px">
  <div class="step-num">3</div><div class="step-title">Keep it Simple</div>
  <p class="step-text">No planning, no stress... Just arrive at your destination and our guides will take it from there!</p>
</div>
<div class="abs step" style="left:733px;top:2267px;width:295px">
  <div class="step-num">4</div><div class="step-title">Fellow Nomads</div>
  <p class="step-text">For group trips, you will meet like-minded folk within the Nomad Ledger community on your adventures.</p>
</div>
<div class="abs step right-align" style="left:166px;top:2427px;width:210px">
  <div class="step-num">5</div><div class="step-title">Customer Experience</div>
  <p class="step-text">After booking a trip, all correspondence is done through Parley, which is quick, easy and efficient.</p>
</div>
<div class="abs step" style="left:603px;top:2668px;width:280px">
  <div class="step-num">6</div><div class="step-title">Pure Crypto Baby!</div>
  <p class="step-text">The world’s first travel agency to exclusively accept cryptocurrencies.<br>That’s right, we’re a crypto only zone... Sorry fiats, there’s no room for you here!</p>
</div>

<!-- NFT collection -->
<h2 class="abs display section-title" style="top:3082px">Nomad Ledger</h2>

<div class="abs nft" style="left:141px;top:3173px;background:radial-gradient(circle at 50% 45%,#d9c894,#7a6a2c 80%)" role="img" aria-label="NFT artwork of a rabbit-eared character with sunglasses on a gold background"></div>
<div class="abs nft" style="left:376px;top:3173px;background:radial-gradient(circle at 50% 45%,#9fd4df,#1f6478 80%)" role="img" aria-label="NFT artwork of a blue rabbit-eared character on a teal background"></div>
<div class="abs nft" style="left:611px;top:3173px;background:radial-gradient(circle at 50% 45%,#c79be6,#4b1f8a 80%)" role="img" aria-label="NFT artwork of a purple rabbit-eared character in a cap on a violet background"></div>
<div class="abs nft" style="left:845px;top:3173px;background:radial-gradient(circle at 50% 45%,#a9dc8f,#2d7a2a 80%)" role="img" aria-label="NFT artwork of a purple rabbit-eared character on a green background"></div>
<div class="abs nft" style="left:141px;top:3400px;background:radial-gradient(circle at 50% 45%,#e59ad4,#7a1f70 80%)" role="img" aria-label="NFT artwork of a teal character in a cowboy hat on a magenta background"></div>
<div class="abs nft" style="left:376px;top:3400px;background:radial-gradient(circle at 50% 45%,#e89a8a,#8a1f22 80%)" role="img" aria-label="NFT artwork of a blue rabbit-eared character on a red background"></div>
<div class="abs nft" style="left:611px;top:3400px;background:radial-gradient(circle at 50% 45%,#e2c08a,#7a4a1c 80%)" role="img" aria-label="NFT artwork of a character in a fur hat on a brown background"></div>
<div class="abs nft" style="left:845px;top:3400px;background:radial-gradient(circle at 50% 45%,#9fc9d8,#22566a 80%)" role="img" aria-label="NFT artwork of a tiger-striped character in armour on a teal background"></div>

<div class="abs explore-btn">Explore Our NFTs</div>

<!-- Footer -->
<footer class="abs site-footer"></footer>
<p class="abs copyright">Copyright © 2022 Company Name. All Rights Reserved.</p>
<div class="abs name-badge footer-badge">Nomad<br>Ledger</div>
<p class="abs legal">Terms &amp; Conditions &nbsp;|&nbsp; Privacy Policy</p>
<span class="abs social" style="left:945px"></span>
<span class="abs social" style="left:975px"></span>
<span class="abs social" style="left:1005px"></span>
<span class="abs social" style="left:1035px"></span>

</body>
</html>
```